Novexa company website, a website for employment for people with autism

The website will make a match between people and jobs, mainly in the graphical sector, but also other sectors.
The name of the company is novexa and automates jobs with people that are on the autism spectrum.
The whole matchmaking and feedback process and so doesn't have to be in this prototype, we just want the general information pages and to convey a great look and brand identity that we will keep in the other pages to be developed. The website must be made with Wordpress, since the backend will be developed in Wordpress too.
It is a social project that wants to create possibilites for people with ASS to work from home for an employer or to do a variety of tasks for different customers.
The people we hire are generally not on the regular job market or have difficulty finding a job and "selling themselves"

Target Market(s)

matchmaking between talent (with ASS) and employers / jobs

Number of Pages Required

5+ page

Font styles to use
Sans Serif

Colors
ec1f27
e34298
a64599
6b449b
0355a3
0792cd

Requirements
Must have
• A stunning landing pages
• Integrate our logo and must match with what will do. We want a clean, modern, minimalistic, sleek website that radiates creativity and good looks.
• We have one page describing what we can do for customers, one page for people with ASS that would like to be candidates (our approach, learning program, ...), two pages that are addressed to partners who want to cooperate: the one's that can assist with autism related assistance and the one's that can help with the job coaching.
Nice to have
• In our logo are many colors as we embrace diversity and want to show that. Out main branding colors are red (for action) and blue for stability and will all gradients that go with it. Mainly white or black (or anthracite) for other parts
Should not have
• We want a modern and minimalistic design, no fluffy designs with lots of ornaments.

```html
<!DOCTYPE html>
<html lang="en">
<head>
<meta charset="utf-8">
<title>Novexa</title>
<link href="https://fonts.googleapis.com/css2?family=Montserrat:wght@400;500;600;700&family=Barlow:wght@400;500;600&display=swap" rel="stylesheet">
<style>
:root{
  --red:#ec1f27;--pink:#e34298;--violet:#a64599;--purple:#6b449b;--blue:#0355a3;--sky:#0792cd;
  --ink:#222;--text:#444;--muted:#6d6d6d;--panel:#ebebeb;--band:#f2f2f2;--white:#fff;
}
*{margin:0;padding:0;box-sizing:border-box}
html,body{width:1200px;height:4000px;overflow:hidden;background:var(--white)}
body{position:relative;font-family:'Barlow',sans-serif;color:var(--text)}
.abs{position:absolute}
h1,h2,h3,.brand,.nav,.btn{font-family:'Montserrat',sans-serif}

/* header */
.brand{font-weight:700;color:var(--ink);letter-spacing:4px;display:flex;align-items:center;gap:12px}
.brand .dot{width:30px;height:30px;border-radius:50%;background:var(--sky)}
.site-brand{left:112px;top:52px;font-size:34px}
.call{right:112px;top:24px;font-family:'Montserrat',sans-serif;font-weight:700;font-size:22px;color:var(--ink);display:flex;align-items:center;gap:8px}
.call span{color:var(--red)}
.nav{right:112px;top:74px;display:flex;gap:44px;font-size:15px;font-weight:600;color:var(--ink)}

/* hero */
.hero{left:0;top:117px;width:1200px;height:590px;background:linear-gradient(100deg,#7a1c3c 0%,#e34298 30%,#8a3ea0 50%,#3a4fd0 70%,#0a2a7a 100%)}
.play{left:562px;top:383px;width:76px;height:76px;border-radius:50%;background:var(--white);display:flex;align-items:center;justify-content:center}

/* bands */
.band{background:var(--band)}

/* about */
.about-art{left:88px;top:782px}
.about-title{left:677px;top:875px;font-size:38px;font-weight:500;color:var(--ink);letter-spacing:1px}
.about-copy{left:677px;top:936px;width:390px;font-size:15px;line-height:26px;color:var(--text)}
.btn{display:flex;align-items:center;justify-content:center;background:var(--blue);color:var(--white);border-radius:24px;font-size:14px;font-weight:600;letter-spacing:.5px}
.about-btn{left:677px;top:1141px;width:131px;height:43px}

/* sections */
.section-title{left:0;width:1200px;text-align:center;font-size:38px;font-weight:500;color:var(--ink);letter-spacing:1px}
.section-lead{left:230px;width:740px;text-align:center;font-size:15px;line-height:27px}

/* projects */
.project-panel{background:var(--panel)}
.project-photo{}
.project-name{font-family:'Montserrat',sans-serif;font-size:20px;font-weight:600;color:var(--ink)}
.project-text{font-size:14px;line-height:24px;width:350px}
.view-btn{left:533px;top:2571px;width:134px;height:43px}

/* why */
.feature-title{font-size:20px;font-weight:600;color:var(--ink);font-family:'Montserrat',sans-serif}
.feature-rule{height:3px;width:76px}
.feature-text{font-size:15px;line-height:26px;width:200px}

/* newsletter */
.newsletter{left:112px;top:3299px;width:976px;height:250px;border-radius:27px;background:linear-gradient(100deg,var(--red) 0%,#b3205a 45%,var(--purple) 70%,var(--blue) 100%);overflow:hidden}
.news-art{left:22px;top:25px;width:200px;height:200px;background:linear-gradient(135deg,#ffffff 0%,#f4c6cc 100%);clip-path:polygon(25% 5%,75% 5%,100% 50%,75% 95%,25% 95%,0 50%)}
.news-title{left:248px;top:42px;font-size:36px;font-weight:600;color:var(--white)}
.news-sub{left:248px;top:98px;font-size:15px;font-style:italic;color:var(--white)}
.news-form{left:245px;top:141px;width:670px;height:51px;border-radius:26px;background:var(--white);display:flex;overflow:hidden}
.news-form .field{flex:1;padding-left:26px;display:flex;align-items:center;font-size:15px;color:var(--ink)}
.news-form .send{width:118px;background:var(--red);color:var(--white);display:flex;align-items:center;justify-content:center;font-family:'Montserrat',sans-serif;font-weight:600;font-size:16px}

/* footer */
.footer-brand{left:112px;top:3590px;font-size:26px}
.social{left:955px;top:3601px;display:flex;gap:5px}
.social i{display:block;width:28px;height:28px;border-radius:50%}
.col-title{font-size:17px;font-weight:500;color:var(--ink)}
.col-list{list-style:none;font-size:13px;line-height:21.5px;color:var(--text)}
.contact-row{display:flex;gap:22px;align-items:flex-start;font-size:13px;line-height:20px}
.footer-rule{left:112px;top:3920px;width:1050px;height:1px;background:#ddd}
.copyright{left:0;width:1200px;top:3950px;text-align:center;font-size:14px;color:var(--ink)}
</style>
</head>
<body>

<header>
  <div class="abs brand site-brand"><i class="dot"></i>NOVEXA</div>
  <div class="abs call">
    <svg width="18" height="18" viewBox="0 0 24 24"><path d="M6.6 10.8a15 15 0 0 0 6.6 6.6l2.2-2.2a1 1 0 0 1 1-.25 11.4 11.4 0 0 0 3.6.6 1 1 0 0 1 1 1V20a1 1 0 0 1-1 1A17 17 0 0 1 3 4a1 1 0 0 1 1-1h3.5a1 1 0 0 1 1 1c0 1.25.2 2.45.6 3.6a1 1 0 0 1-.25 1z" fill="#ec1f27"/></svg>
    CALL US:<span>555.014.2290</span>
  </div>
  <nav class="abs nav"><span>HOME</span><span>ABOUT</span><span>SERVICES</span><span>PROJECTS</span><span>NEWS</span><span>CONTACT</span></nav>
</header>

<section class="abs hero" role="img" aria-label="Video still: swirling pink and blue coloured smoke"></section>
<div class="abs play"><svg width="30" height="32" viewBox="0 0 30 32"><path d="M4 2 28 16 4 30z" fill="#ec1f27"/></svg></div>

<!-- about -->
<div class="abs band" style="left:0;top:707px;width:75px;height:407px"></div>
<div class="abs band" style="left:98px;top:707px;width:108px;height:475px"></div>
<div class="abs band" style="left:283px;top:707px;width:75px;height:60px"></div>
<svg class="abs about-art" width="580" height="570" viewBox="0 0 580 570" role="img" aria-label="Hexagon collage: photos of a woman helping a colleague and a smiling young woman">
  <defs><linearGradient id="hexGrad" x1="0" y1="0" x2="1" y2="1"><stop offset="0" stop-color="#e34298"/><stop offset="1" stop-color="#0355a3"/></linearGradient></defs>
  <polygon points="70,127 170,127 242,262 170,397 70,397 5,262" fill="url(#hexGrad)"/>
  <polygon points="198,5 470,5 567,195 470,385 198,385 110,195" fill="#c9a68e"/>
  <polygon points="176,335 364,335 430,448 364,565 176,565 110,448" fill="#d9cfc6"/>
</svg>
<h2 class="abs about-title">ABOUT US</h2>
<p class="abs about-copy">Sed ut perspiciatis unde omnis iste natus error sitvoluptatem accusantium doloremque laudantium, totamaque ipsa quae ab illo inventore veritatis et quasi architecto beatae vitae dic ta sunt explicabomo enimtatemed ut perspiciatis unde omnis iste natus error sitvoluptatem accusantium doloremque laud antium, totamaque ipsa quae ab illo inventore veritatis et qu asi architecto beatae vitae dic ta sunt explicabomo</p>
<div class="abs btn about-btn">READ MORE</div>

<!-- projects -->
<h2 class="abs section-title" style="top:1452px">PROJECTS</h2>
<p class="abs section-lead" style="top:1510px">Sed ut perspiciatis unde omnis iste natus error sit voluptatem accusantium doloremque laudantium, totamaque ipsa quae ab illo inventore veritatis et quasi architecto beatae vitae dicta sunt explicabomo enimtatem.</p>

<div class="abs project-panel" style="left:147px;top:1792px;width:432px;height:261px"></div>
<div class="abs project-photo" style="left:112px;top:1616px;width:424px;height:299px;background:#c8c2bb" role="img" aria-label="Photo: a young woman and a man reviewing papers at a kitchen table"></div>
<h3 class="abs project-name" style="left:184px;top:1943px">Project Name</h3>
<p class="abs project-text" style="left:184px;top:1978px">Sed ut perspiciatis unde omnis iste nat sit voluptatem accusantium doloremque laudantium, totariaa.</p>

<div class="abs project-panel" style="left:656px;top:1792px;width:432px;height:261px"></div>
<div class="abs project-photo" style="left:619px;top:1616px;width:426px;height:299px;background:linear-gradient(135deg,#a64599,#e34298)" role="img" aria-label="Photo with purple tint: two women talking on a sofa"></div>
<h3 class="abs project-name" style="left:693px;top:1943px">Project Name</h3>
<p class="abs project-text" style="left:693px;top:1978px">Sed ut perspiciatis unde omnis iste nat sit voluptatem accusantium doloremque laudantium, totariaa.</p>

<div class="abs project-panel" style="left:147px;top:2264px;width:432px;height:261px"></div>
<div class="abs project-photo" style="left:112px;top:2088px;width:424px;height:296px;background:linear-gradient(135deg,#0792cd,#0355a3)" role="img" aria-label="Photo with blue tint: two men working together at a desk"></div>
<h3 class="abs project-name" style="left:184px;top:2415px">Project Name</h3>
<p class="abs project-text" style="left:184px;top:2450px">Sed ut perspiciatis unde omnis iste nat sit voluptatem accusantium doloremque laudantium, totariaa.</p>

<div class="abs project-panel" style="left:656px;top:2264px;width:432px;height:261px"></div>
<div class="abs project-photo" style="left:619px;top:2088px;width:426px;height:296px;background:#d3d6d6" role="img" aria-label="Photo: an older man and a younger man sharing a laptop"></div>
<h3 class="abs project-name" style="left:693px;top:2415px">Project Name</h3>
<p class="abs project-text" style="left:693px;top:2450px">Sed ut perspiciatis unde omnis iste nat sit voluptatem accusantium doloremque laudantium, totariaa.</p>

<div class="abs btn view-btn">VIEW ALL</div>

<!-- why -->
<h2 class="abs section-title" style="top:2716px">WHY CHOOSE NOVEXA</h2>
<p class="abs section-lead" style="top:2785px">Sed ut perspiciatis unde omnis iste natus error sit voluptatem accusantium doloremque laudantium, totamaque ipsa quae ab illo inventore veritatis et quasi architecto beatae vitae dicta sunt explicabomo enimtatem.</p>

<svg class="abs" style="left:112px;top:2885px" width="70" height="70" viewBox="0 0 70 70" fill="none" stroke="#0355a3" stroke-width="3"><circle cx="35" cy="30" r="16"/><path d="M28 50h14M29 57h12"/><path d="M35 4v6M60 30h-6M16 30h-6M53 12l-4 4M17 12l4 4"/></svg>
<svg class="abs" style="left:371px;top:2885px" width="70" height="70" viewBox="0 0 70 70" fill="none" stroke="#ec1f27" stroke-width="3"><path d="M20 64V50a24 24 0 1 1 30-6l4 8h-6v8H36v4"/><circle cx="34" cy="28" r="10"/></svg>
<svg class="abs" style="left:629px;top:2885px" width="70" height="70" viewBox="0 0 70 70" fill="none" stroke="#6b449b" stroke-width="3"><circle cx="32" cy="38" r="26"/><circle cx="32" cy="38" r="16"/><circle cx="32" cy="38" r="6"/><path d="M32 38 60 10M52 8v10h10"/></svg>
<svg class="abs" style="left:888px;top:2885px" width="70" height="70" viewBox="0 0 70 70" fill="none" stroke="#e34298" stroke-width="3"><rect x="26" y="6" width="38" height="26" rx="2"/><path d="m26 8 19 14 19-14"/><path d="M8 34c0 14 14 28 28 28l5-7-8-6-4 4c-5-2-10-7-12-12l4-4-6-8z"/></svg>

<h3 class="abs feature-title" style="left:112px;top:2985px">Suptacusantium</h3>
<div class="abs feature-rule" style="left:112px;top:3022px;background:var(--blue)"></div>
<p class="abs feature-text" style="left:112px;top:3040px">Sed ut perspiciatis unde omnis iste natuserror sit voluptlortm accusantium dolorlaloru dalolu mtotam rem aperiam, eaquesa quae ab illo inventor.</p>
<h3 class="abs feature-title" style="left:371px;top:2985px">Suptacusantium</h3>
<div class="abs feature-rule" style="left:371px;top:3022px;background:var(--red)"></div>
<p class="abs feature-text" style="left:371px;top:3040px">Sed ut perspiciatis unde omnis iste natuserror sit voluptlortm accusantium dolorlaloru dalolu mtotam rem aperiam, eaquesa quae ab illo inventor.</p>
<h3 class="abs feature-title" style="left:629px;top:2985px">Suptacusantium</h3>
<div class="abs feature-rule" style="left:629px;top:3022px;background:var(--purple)"></div>
<p class="abs feature-text" style="left:629px;top:3040px">Sed ut perspiciatis unde omnis iste natuserror sit voluptlortm accusantium dolorlaloru dalolu mtotam rem aperiam, eaquesa quae ab illo inventor.</p>
<h3 class="abs feature-title" style="left:888px;top:2985px">Suptacusantium</h3>
<div class="abs feature-rule" style="left:888px;top:3022px;background:var(--pink)"></div>
<p class="abs feature-text" style="left:888px;top:3040px">Sed ut perspiciatis unde omnis iste natuserror sit voluptlortm accusantium dolorlaloru dalolu mtotam rem aperiam, eaquesa quae ab illo inventor.</p>

<!-- newsletter -->
<section class="abs newsletter">
  <div class="abs news-art" role="img" aria-label="Illustration: white hexagon cluster"></div>
  <h2 class="abs news-title">Sign up to our newsletter</h2>
  <p class="abs news-sub">Neque porro quisquam est qui dolorem ipsum quia dolor sit amet, consectetu</p>
  <div class="abs news-form"><span class="field">Email:</span><span class="send">SIGN UP</span></div>
</section>

<!-- footer -->
<div class="abs band" style="left:0;top:3600px;width:75px;height:400px"></div>
<div class="abs band" style="left:98px;top:3720px;width:108px;height:280px"></div>
<div class="abs band" style="left:230px;top:3800px;width:80px;height:200px"></div>

<div class="abs brand footer-brand"><i class="dot" style="width:24px;height:24px"></i>NOVEXA</div>
<div class="abs social"><i style="background:#3b5998"></i><i style="background:#1da1f2"></i><i style="background:#0077b5"></i><i style="background:#dd4b39"></i></div>

<h4 class="abs col-title" style="left:110px;top:3690px">Contact</h4>
<div class="abs" style="left:110px;top:3730px;display:flex;flex-direction:column;gap:26px">
  <div class="contact-row"><svg width="22" height="26" viewBox="0 0 22 26" fill="none" stroke="#e34298" stroke-width="2"><path d="M11 24S3 15 3 10a8 8 0 0 1 16 0c0 5-8 14-8 14z"/><circle cx="11" cy="10" r="3"/></svg><span>120 Harbor Lane,<br>Suite 4, Eastfield</span></div>
  <div class="contact-row"><svg width="22" height="24" viewBox="0 0 24 24" fill="none" stroke="#0355a3" stroke-width="2"><path d="M6.6 10.8a15 15 0 0 0 6.6 6.6l2.2-2.2 4.6 1.4V21A17 17 0 0 1 3 4h4.5l1.2 4.6z"/></svg><span>555 014 2291<br>555 014 2292</span></div>
  <div class="contact-row"><svg width="22" height="18" viewBox="0 0 22 18" fill="none" stroke="#ec1f27" stroke-width="2"><rect x="1" y="1" width="20" height="16"/><path d="m1 2 10 8 10-8"/></svg><span>hello@novexa-mail.com<br>team@novexa-mail.com</span></div>
</div>

<h4 class="abs col-title" style="left:413px;top:3690px">Projects</h4>
<ul class="abs col-list" style="left:413px;top:3728px"><li>Lorem ipsum dolo</li><li>Consectetur adipiscing elit.</li><li>Fusce eget leo tincid</li><li>Donec consequat</li><li>Praesent elementum</li><li>Jmauris posuerel</li><li>Aenean a ex eu lectu</li></ul>
<ul class="abs col-list" style="left:661px;top:3728px"><li>Lorem ipsum dolo</li><li>Consectetur adipiscing elit.</li><li>Fusce eget leo tincid</li><li>Donec consequat</li><li>Praesent elementum</li><li>Jmauris posuerel</li><li>Aenean a ex eu lectu</li></ul>
<h4 class="abs col-title" style="left:923px;top:3690px">Other Links</h4>
<ul class="abs col-list" style="left:923px;top:3728px"><li>Lorem ipsum dolo</li><li>Consectetur adipiscing elit.</li><li>Fusce eget leo tincid</li><li>Donec consequat</li><li>Praesent elementum</li><li>Jmauris posuerel</li><li>Aenean a ex eu lectu</li></ul>

<div class="abs footer-rule"></div>
<p class="abs copyright">Copyright 2019 All Rights Reserved</p>

</body>
</html>
```